Tideline Homecraft Business Card Design

We need a business card for an established builder of high quality bespoke homes in Auckland and Northland. We build and renovate homes collaboratively facilitating effective communication between owners, builders, architects, suppliers and tradespeople. We have never built or renovated a home that leaks or has faults. We only use reliable materials. We have never been sued or had legal action taken against us. We are honest builders of bespoke homes not group mass produced homes. Our niche market is in character homes. We practice sustainability and have built a lot of coastal property. We have been in business for over thirty years . We would like to see natural colors of the environment sand,sea and maybe vegetation . The design should communicate quality, sustainability,fair pricing, open communication and the originality of bespoke building. And the fact that the builder is registered.

Industry/Entity Type

Business

Contact Information for Business Card

Rowan Tellick Builders
Ph. 021583917
18 Kestrel Rd Harwood Bay Auckland 0814
PO Box 927 Mangawhai 0583

```html
<!DOCTYPE html>
<html lang="en">
<head>
<meta charset="utf-8">
<title>Tideline Homecraft – Business Card</title>
<link rel="stylesheet" href="https://fonts.googleapis.com/css2?family=Open+Sans:wght@400;600;800&display=swap">
<style>
  :root {
    --backdrop: #2b2d31;
    --sea-deep: #1f5a68;
    --sea-light: #2f7583;
    --sand: #f4ecdc;
    --sand-warm: #e6d6b8;
    --vegetation: #4d6b3c;
    --ink-dark: #34403a;
    --ink-body: #232a26;
  }
  * { margin: 0; padding: 0; box-sizing: border-box; }
  html, body {
    width: 1200px;
    height: 864px;
    overflow: hidden;
    background: var(--backdrop);
    font-family: "Open Sans", Arial, sans-serif;
  }
  .canvas {
    position: relative;
    width: 1200px;
    height: 864px;
  }
  .card {
    position: absolute;
    left: 340px;
    width: 520px;
    height: 300px;
    box-shadow: 0 10px 28px rgba(0,0,0,.45);
    overflow: hidden;
  }
  .card-front {
    top: 110px;
    background: linear-gradient(160deg, var(--sea-light) 0%, var(--sea-deep) 70%);
  }
  .front-shore {
    position: absolute;
    left: 0;
    right: 0;
    bottom: 0;
    height: 16px;
    background: var(--sand-warm);
  }
  .front-shore::before {
    content: "";
    position: absolute;
    left: 0;
    right: 0;
    top: -6px;
    height: 6px;
    background: var(--vegetation);
  }
  .front-name {
    position: absolute;
    right: 34px;
    bottom: 50px;
    color: var(--sand);
    font-weight: 800;
    font-size: 34px;
    letter-spacing: .2px;
  }
  .card-back {
    top: 454px;
    background: var(--sand);
  }
  .back-brand {
    position: absolute;
    right: 34px;
    top: 40px;
    display: flex;
    align-items: center;
    gap: 10px;
    color: var(--ink-dark);
    font-weight: 800;
    font-size: 30px;
  }
  .back-brand .brand-mark {
    width: 14px;
    height: 14px;
    border-radius: 50%;
    background: var(--vegetation);
  }
  .holder-name {
    position: absolute;
    left: 28px;
    top: 116px;
    color: var(--vegetation);
    font-size: 17px;
    font-weight: 600;
  }
  .divider {
    position: absolute;
    left: 0;
    right: 0;
    top: 146px;
    height: 1px;
    background: var(--sea-deep);
  }
  .contact {
    position: absolute;
    right: 34px;
    top: 178px;
    text-align: right;
    color: var(--ink-body);
    font-size: 15px;
    line-height: 23px;
    font-style: normal;
  }
  .contact .phone {
    display: flex;
    justify-content: flex-end;
    align-items: center;
    gap: 8px;
  }
  .contact .phone svg { width: 12px; height: 12px; fill: var(--sea-deep); }
</style>
</head>
<body>
<main class="canvas">
  <section class="card card-front" aria-label="Card front">
    <p class="front-name">Tideline Homecraft</p>
    <div class="front-shore" aria-hidden="true"></div>
  </section>

  <section class="card card-back" aria-label="Card back">
    <div class="back-brand">
      <span class="brand-name">Tideline Homecraft</span>
      <span class="brand-mark" aria-hidden="true"></span>
    </div>
    <p class="holder-name">Rowan Tellick Builders</p>
    <div class="divider"></div>
    <address class="contact">
      <div class="phone">
        <span>021583917</span>
        <svg viewBox="0 0 24 24" aria-hidden="true"><path d="M6.6 10.8a15.1 15.1 0 0 0 6.6 6.6l2.2-2.2a1 1 0 0 1 1-.25 11.4 11.4 0 0 0 3.6.57 1 1 0 0 1 1 1V20a1 1 0 0 1-1 1A17 17 0 0 1 3 4a1 1 0 0 1 1-1h3.5a1 1 0 0 1 1 1c0 1.25.2 2.45.57 3.57a1 1 0 0 1-.25 1z"/></svg>
      </div>
      <div>18 Kestrel Rd Harwood</div>
      <div>Bay Auckland 0814</div>
      <div>PO Box 927 Mangawhai 0583</div>
    </address>
  </section>
</main>
</body>
</html>
```